Dental Medical History Form - Content provided

Design a medical history form for a dental practice. Content is provided so all that is needed is the formatting to make it look great and easy to read.

"Patient Information" to include all information contained in top portion of the "Patient Medical History Form" docx file.

"Medical History" should follow the formatting and content of the "Exact Medical History" file as this is what the entry fields look like in our practice software and so we would like it to match.

1st page - Patient info, allergies, medications, antibiotics, joint replacement, pregnancy.

2nd page - Do you have, or have you had, any of the following? . . . . . . .
Updates

Target Market(s)

All ages but must be clear enough for elderly to read. Use as much space as possible to keep font size bigger yet keep to two pages

Industry/Entity Type

Dental

Font styles to use
Sans Serif

Requirements
Must have
• All content provided
• Our logo at the top (file provided)
• Century Gothic Font
• Limit to two pages

```html
<!DOCTYPE html>
<html lang="en">
<head>
<meta charset="utf-8">
<title>Harbour Dental – Confidential Medical History</title>
<link href="https://fonts.googleapis.com/css2?family=Mulish:ital,wght@0,400;0,700;0,800;1,400&display=swap" rel="stylesheet">
<style>
:root{
  --bg:#e4e2df;
  --paper:#ffffff;
  --ink:#1d1d1d;
  --rule:#555555;
  --band-dark:#4a4c4f;
  --band-light:#d4d5d6;
  --logo:#6b6d70;
}
*{box-sizing:border-box;margin:0;padding:0}
html,body{width:1200px;height:900px;overflow:hidden;background:var(--bg)}
body{font-family:"Mulish",sans-serif;color:var(--ink);position:relative}
.page{position:absolute;top:66px;width:549px;height:769px;background:var(--paper);box-shadow:0 2px 8px rgba(0,0,0,.25)}
.page--patient{left:47px}
.page--history{left:620px}
.abs{position:absolute}
.brand{font-size:23px;font-weight:400;color:var(--logo);letter-spacing:.3px;line-height:1}
.title-band{position:absolute;left:258px;top:36px;width:291px;height:22px}
.title-band > svg{position:absolute;inset:0}
.title-band span{position:absolute;left:22px;top:3px;color:#fff;font-weight:800;font-size:14px;letter-spacing:.2px}
.field{position:absolute;display:flex;align-items:flex-end;font-size:10px;line-height:12px}
.field .line{flex:1;border-bottom:1px solid var(--rule);margin-left:4px;height:9px}
.sub{position:absolute;font-size:5px;color:#333}
.heading{position:absolute;font-weight:700;font-size:10.5px}
.text{position:absolute;font-size:10px;line-height:12px;white-space:nowrap}
.box{display:inline-block;width:7px;height:7px;border:1px solid var(--ink);margin-right:3px;vertical-align:0}
.opts{position:absolute;display:flex;gap:12px;font-size:10px;line-height:12px;white-space:nowrap}
.rule{position:absolute;border-bottom:1px solid var(--rule)}
.footer{position:absolute;left:0;top:729px;width:549px;height:15px}
.footer > .band{position:absolute;left:0;top:0}
.footer .phone{position:absolute;left:38px;top:0;font-size:11px;font-weight:700;line-height:15px;display:flex;align-items:center;gap:5px}
.footer .addr{position:absolute;left:182px;top:0;font-size:10.5px;color:#fff;line-height:15px;display:flex;align-items:center;gap:5px;white-space:nowrap}
.footer .icon{flex:none;display:block}
.col{position:absolute;width:250px}
.col h3{font-weight:700;font-size:9.5px;line-height:13px}
.q{position:relative;height:13px;font-size:9px;line-height:13px;white-space:nowrap}
.q .yn{position:absolute;left:177px;top:0;display:flex;gap:5px}
.q .yn .box{width:6px;height:6px}
.col--right .q .yn{left:178px}
.gap{height:11px}
.thanks{position:absolute;left:225px;top:689px;font-size:6.5px;font-style:italic;line-height:9px;width:300px}
</style>
</head>
<body>

<section class="page page--patient">
  <div class="brand abs" style="left:28px;top:34px">harbour dental</div>
  <div class="title-band">
    <svg width="291" height="22" viewBox="0 0 291 22"><polygon points="10,0 291,0 291,22 0,22" fill="var(--band-dark)"/></svg>
    <span>CONFIDENTIAL MEDICAL HISTORY</span>
  </div>

  <div class="field" style="left:28px;top:92px;width:237px">Name :<span class="line"></span></div>
  <span class="sub" style="left:83px;top:105px">First</span>
  <span class="sub" style="left:157px;top:105px">Middle</span>
  <span class="sub" style="left:228px;top:105px">Last</span>
  <div class="field" style="left:28px;top:118px;width:237px">Address :<span class="line"></span></div>
  <div class="field" style="left:28px;top:143px;width:237px">DOB :<span class="line"></span></div>
  <div class="field" style="left:28px;top:169px;width:237px">Email Address :<span class="line"></span></div>
  <div class="field" style="left:28px;top:195px;width:237px">Phone Number(s) :<span class="line"></span></div>
  <span class="sub" style="left:139px;top:208px">Mobile</span>
  <span class="sub" style="left:191px;top:208px">Work</span>
  <span class="sub" style="left:234px;top:208px">Home</span>

  <div class="heading" style="left:283px;top:92px">General Practitioner</div>
  <div class="field" style="left:283px;top:117px;width:237px">Name :<span class="line"></span></div>
  <div class="field" style="left:283px;top:143px;width:237px">Practice Name :<span class="line"></span></div>
  <div class="field" style="left:283px;top:169px;width:237px">Phone Number :<span class="line"></span></div>
  <div class="text" style="left:283px;top:195px">Do you have a health fund with<br>dental cover?</div>
  <div class="opts" style="left:441px;top:208px"><span><span class="box"></span>Yes</span><span><span class="box"></span>No</span></div>
  <div class="text" style="left:283px;top:234px">If so, what is the name of the fund?</div>
  <div class="text" style="left:283px;top:260px">Fund Number?</div>
  <div class="text" style="left:283px;top:286px">Priority Number of card :&nbsp; 0&nbsp; 1&nbsp; 2&nbsp; 3&nbsp; 4&nbsp; 5</div>

  <div class="heading" style="left:28px;top:248px">Emergency Contact Person</div>
  <div class="field" style="left:28px;top:273px;width:237px">Name :<span class="line"></span></div>
  <div class="field" style="left:28px;top:299px;width:237px">Relationship :<span class="line"></span></div>
  <div class="field" style="left:28px;top:324px;width:237px">Phone Number :<span class="line"></span></div>

  <div class="heading" style="left:28px;top:351px">Please indicate if you are allergic to any of the following <span class="box" style="width:8px;height:8px"></span>?</div>
  <div class="opts" style="left:28px;top:377px"><span><span class="box"></span>Aspirin</span><span><span class="box"></span>Codeine</span><span><span class="box"></span>Penicillin</span><span><span class="box"></span>Sulfites</span><span><span class="box"></span>Latex</span><span><span class="box"></span>Local Anaesthetic</span><span><span class="box"></span>Lactose</span><span><span class="box"></span>Nickel</span></div>
  <div class="field" style="left:28px;top:402px;width:492px"><span><span class="box"></span>Other :</span><span class="line"></span></div>

  <div class="heading" style="left:28px;top:430px">Are you currently taking, or have ever taken, any of the following medication <span class="box" style="width:8px;height:8px"></span>?</div>
  <div class="opts" style="left:28px;top:454px"><span><span class="box"></span>Asthma inhaler</span><span><span class="box"></span>Anti-epileptics</span><span><span class="box"></span>Anti-depressants</span><span><span class="box"></span>Blood Pressure</span><span><span class="box"></span>Blood Thinners</span></div>
  <div class="opts" style="left:28px;top:475px"><span><span class="box"></span>Bisphosphonates</span><span><span class="box"></span>Chemotherapy</span><span><span class="box"></span>Insulin</span><span><span class="box"></span>Immunosuppressants</span><span><span class="box"></span>Steroids</span></div>
  <div class="field" style="left:28px;top:500px;width:492px"><span><span class="box"></span>Oral Contraceptive&nbsp;&nbsp;&nbsp; <span class="box"></span>Other :</span><span class="line"></span></div>

  <div class="heading" style="left:28px;top:534px">Please specify medication name, does, and frequency where possible.</div>
  <div class="rule" style="left:28px;top:568px;width:492px"></div>
  <div class="rule" style="left:28px;top:593px;width:492px"></div>
  <div class="rule" style="left:28px;top:619px;width:492px"></div>

  <div class="text" style="left:40px;top:638px">Do you require antibiotic cover?</div>
  <div class="opts" style="left:207px;top:638px"><span><span class="box"></span>Yes</span><span><span class="box"></span>No</span></div>
  <div class="text" style="left:40px;top:664px">Have you had a joint replacement ?</div>
  <div class="opts" style="left:207px;top:664px"><span><span class="box"></span>Yes</span><span><span class="box"></span>No</span></div>
  <div class="heading" style="left:40px;top:688px">Women:</div>
  <div class="text" style="left:40px;top:704px">Are you Pregnant?</div>
  <div class="opts" style="left:137px;top:704px"><span><span class="box"></span>Yes</span><span><span class="box"></span>No</span><span><span class="box"></span>Possible</span></div>
  <div class="text" style="left:283px;top:704px">Breast Feeding?</div>
  <div class="opts" style="left:373px;top:704px"><span><span class="box"></span>Yes</span><span><span class="box"></span>No</span></div>

  <div class="footer">
    <svg class="band" width="549" height="15" viewBox="0 0 549 15"><rect width="549" height="15" fill="var(--band-light)"/><polygon points="172,0 549,0 549,15 165,15" fill="var(--band-dark)"/></svg>
    <div class="phone"><svg class="icon" width="10" height="10" viewBox="0 0 10 10"><circle cx="5" cy="5" r="4.4" fill="none" stroke="#1d1d1d"/><path d="M3.3 2.6c.3-.3.6-.2.8.1l.4.7c.1.3 0 .5-.2.6l-.3.2c.2.6.7 1.1 1.2 1.3l.2-.3c.2-.2.4-.3.6-.2l.7.4c.3.2.3.5.1.8-.4.5-1 .6-1.6.3C4 6.1 3.4 5.4 3 4.6c-.3-.7-.2-1.4.3-2z" fill="#1d1d1d"/></svg><span>(02) 4000 1234</span></div>
    <div class="addr"><svg class="icon" width="7" height="10" viewBox="0 0 7 10"><path d="M3.5 0A3.3 3.3 0 0 0 .2 3.3C.2 5.8 3.5 10 3.5 10s3.3-4.2 3.3-6.7A3.3 3.3 0 0 0 3.5 0zm0 4.6a1.3 1.3 0 1 1 0-2.6 1.3 1.3 0 0 1 0 2.6z" fill="#fff"/></svg><span>Harbour Dental, Suite 4/88 Ocean View Rd, Bayside NSW. 2000</span></div>
  </div>
</section>

<section class="page page--history">
  <div class="heading" style="left:28px;top:27px">Do you have, or have you had, any of the following?</div>

  <div class="col col--left" style="left:28px;top:46px">
    <h3>Dental</h3>
    <div class="q">Acid Reflux<span class="yn"><span><span class="box"></span>Yes</span><span><span class="box"></span>No</span></span></div>
    <div class="q">Bad Breath/Taste<span class="yn"><span><span class="box"></span>Yes</span><span><span class="box"></span>No</span></span></div>
    <div class="q">Bleeding/Swollen/Sore Gums<span class="yn"><span><span class="box"></span>Yes</span><span><span class="box"></span>No</span></span></div>
    <div class="q">Blisters/Ulcers in Mouth<span class="yn"><span><span class="box"></span>Yes</span><span><span class="box"></span>No</span></span></div>
    <div class="q">Broken tooth/filling<span class="yn"><span><span class="box"></span>Yes</span><span><span class="box"></span>No</span></span></div>
    <div class="q">Burning tongue<span class="yn"><span><span class="box"></span>Yes</span><span><span class="box"></span>No</span></span></div>
    <div class="q">Dry mouth<span class="yn"><span><span class="box"></span>Yes</span><span><span class="box"></span>No</span></span></div>
    <div class="q">Food collection between teeth<span class="yn"><span><span class="box"></span>Yes</span><span><span class="box"></span>No</span></span></div>
    <div class="q">Grinding/Clenching teeth (day/night)<span class="yn"><span><span class="box"></span>Yes</span><span><span class="box"></span>No</span></span></div>
    <div class="q">loose teeth<span class="yn"><span><span class="box"></span>Yes</span><span><span class="box"></span>No</span></span></div>
    <div class="q">Crooked teeth<span class="yn"><span><span class="box"></span>Yes</span><span><span class="box"></span>No</span></span></div>
    <div class="q">Discoloured teeth<span class="yn"><span><span class="box"></span>Yes</span><span><span class="box"></span>No</span></span></div>
    <div class="q">Sensitivity to Hot/Cold<span class="yn"><span><span class="box"></span>Yes</span><span><span class="box"></span>No</span></span></div>
    <div class="q">Tooth pain when chewing<span class="yn"><span><span class="box"></span>Yes</span><span><span class="box"></span>No</span></span></div>
    <div class="q">Jaw Pain/Fracture<span class="yn"><span><span class="box"></span>Yes</span><span><span class="box"></span>No</span></span></div>
    <div class="q">orthodontic treatment/history<span class="yn"><span><span class="box"></span>Yes</span><span><span class="box"></span>No</span></span></div>
    <div class="q">Oral Cancer<span class="yn"><span><span class="box"></span>Yes</span><span><span class="box"></span>No</span></span></div>
    <div class="gap"></div>
    <h3>Diet/Lifestyle</h3>
    <div class="q" style="font-size:8px">Drink more than one glass alchohol per day<span class="yn" style="font-size:9px"><span><span class="box"></span>Yes</span><span><span class="box"></span>No</span></span></div>
    <div class="q">Smoking<span class="yn"><span><span class="box"></span>Yes</span><span><span class="box"></span>No</span></span></div>
    <div class="q">Carbonated drinks<span class="yn"><span><span class="box"></span>Yes</span><span><span class="box"></span>No</span></span></div>
    <div class="q">Sugary foods<span class="yn"><span><span class="box"></span>Yes</span><span><span class="box"></span>No</span></span></div>
    <div class="gap"></div>
    <h3>Blood</h3>
    <div class="q">Anaemia<span class="yn"><span><span class="box"></span>Yes</span><span><span class="box"></span>No</span></span></div>
    <div class="q">Blood clots<span class="yn"><span><span class="box"></span>Yes</span><span><span class="box"></span>No</span></span></div>
    <div class="q">Leukemia<span class="yn"><span><span class="box"></span>Yes</span><span><span class="box"></span>No</span></span></div>
    <div class="q">Low platelets<span class="yn"><span><span class="box"></span>Yes</span><span><span class="box"></span>No</span></span></div>
    <div class="q">Lymphoma<span class="yn"><span><span class="box"></span>Yes</span><span><span class="box"></span>No</span></span></div>
    <div class="q">Haemophelia<span class="yn"><span><span class="box"></span>Yes</span><span><span class="box"></span>No</span></span></div>
    <div class="gap"></div>
    <h3>Chest</h3>
    <div class="q">Bronchitis<span class="yn"><span><span class="box"></span>Yes</span><span><span class="box"></span>No</span></span></div>
    <div class="q">Cystic Fibrosis<span class="yn"><span><span class="box"></span>Yes</span><span><span class="box"></span>No</span></span></div>
    <div class="q">Emphysema<span class="yn"><span><span class="box"></span>Yes</span><span><span class="box"></span>No</span></span></div>
    <div class="q">Pneumonia<span class="yn"><span><span class="box"></span>Yes</span><span><span class="box"></span>No</span></span></div>
    <div class="gap"></div>
    <h3>Infectious Disease</h3>
    <div class="q">Creutzfeldt-Jakob Disease<span class="yn"><span><span class="box"></span>Yes</span><span><span class="box"></span>No</span></span></div>
    <div class="q">Hepatitis A,B,C,D<span class="yn"><span><span class="box"></span>Yes</span><span><span class="box"></span>No</span></span></div>
    <div class="q">HIV/AIDS<span class="yn"><span><span class="box"></span>Yes</span><span><span class="box"></span>No</span></span></div>
    <div class="q">Influenza<span class="yn"><span><span class="box"></span>Yes</span><span><span class="box"></span>No</span></span></div>
    <div class="q">Shingles<span class="yn"><span><span class="box"></span>Yes</span><span><span class="box"></span>No</span></span></div>
    <div class="q">Tuberculosis<span class="yn"><span><span class="box"></span>Yes</span><span><span class="box"></span>No</span></span></div>
  </div>

  <div class="col col--right" style="left:285px;top:46px">
    <h3>Heart</h3>
    <div class="q">Angina<span class="yn"><span><span class="box"></span>Yes</span><span><span class="box"></span>No</span></span></div>
    <div class="q">Atrial fibrillation<span class="yn"><span><span class="box"></span>Yes</span><span><span class="box"></span>No</span></span></div>
    <div class="q">Blood Pressure (high/low)<span class="yn"><span><span class="box"></span>Yes</span><span><span class="box"></span>No</span></span></div>
    <div class="q">Congenital heart disease<span class="yn"><span><span class="box"></span>Yes</span><span><span class="box"></span>No</span></span></div>
    <div class="q">Heart attack<span class="yn"><span><span class="box"></span>Yes</span><span><span class="box"></span>No</span></span></div>
    <div class="q">Heart murmur<span class="yn"><span><span class="box"></span>Yes</span><span><span class="box"></span>No</span></span></div>
    <div class="q">Heart surgery<span class="yn"><span><span class="box"></span>Yes</span><span><span class="box"></span>No</span></span></div>
    <div class="q">Heart valve replacement<span class="yn"><span><span class="box"></span>Yes</span><span><span class="box"></span>No</span></span></div>
    <div class="q">Infective endocarditis<span class="yn"><span><span class="box"></span>Yes</span><span><span class="box"></span>No</span></span></div>
    <div class="q">Rheumatic heart disease<span class="yn"><span><span class="box"></span>Yes</span><span><span class="box"></span>No</span></span></div>
    <div class="q">Pacemaker<span class="yn"><span><span class="box"></span>Yes</span><span><span class="box"></span>No</span></span></div>
    <div class="q">Stent<span class="yn"><span><span class="box"></span>Yes</span><span><span class="box"></span>No</span></span></div>
    <div class="gap"></div>
    <h3>Other</h3>
    <div class="q">Anxiety/PTSD<span class="yn"><span><span class="box"></span>Yes</span><span><span class="box"></span>No</span></span></div>
    <div class="q">Arthritis<span class="yn"><span><span class="box"></span>Yes</span><span><span class="box"></span>No</span></span></div>
    <div class="q">Alzheimer's<span class="yn"><span><span class="box"></span>Yes</span><span><span class="box"></span>No</span></span></div>
    <div class="q">Asthma<span class="yn"><span><span class="box"></span>Yes</span><span><span class="box"></span>No</span></span></div>
    <div class="q">Anaphylaxis<span class="yn"><span><span class="box"></span>Yes</span><span><span class="box"></span>No</span></span></div>
    <div class="q">Auto-immune disease<span class="yn"><span><span class="box"></span>Yes</span><span><span class="box"></span>No</span></span></div>
    <div class="q">Coeliac<span class="yn"><span><span class="box"></span>Yes</span><span><span class="box"></span>No</span></span></div>
    <div class="q">Depression<span class="yn"><span><span class="box"></span>Yes</span><span><span class="box"></span>No</span></span></div>
    <div class="q">Diabetes<span class="yn"><span><span class="box"></span>Yes</span><span><span class="box"></span>No</span></span></div>
    <div class="q">Epilepsy<span class="yn"><span><span class="box"></span>Yes</span><span><span class="box"></span>No</span></span></div>
    <div class="q">Kidney disease<span class="yn"><span><span class="box"></span>Yes</span><span><span class="box"></span>No</span></span></div>
    <div class="q">Liver disease<span class="yn"><span><span class="box"></span>Yes</span><span><span class="box"></span>No</span></span></div>
    <div class="q">Osteoporosis<span class="yn"><span><span class="box"></span>Yes</span><span><span class="box"></span>No</span></span></div>
    <div class="q">Parkinson's<span class="yn"><span><span class="box"></span>Yes</span><span><span class="box"></span>No</span></span></div>
    <div class="q">Radiation to head/neck<span class="yn"><span><span class="box"></span>Yes</span><span><span class="box"></span>No</span></span></div>
    <div class="q">Schizophrenia<span class="yn"><span><span class="box"></span>Yes</span><span><span class="box"></span>No</span></span></div>
    <div class="q">Snoring<span class="yn"><span><span class="box"></span>Yes</span><span><span class="box"></span>No</span></span></div>
    <div class="q">Sleep apnea<span class="yn"><span><span class="box"></span>Yes</span><span><span class="box"></span>No</span></span></div>
    <div class="q">Stroke<span class="yn"><span><span class="box"></span>Yes</span><span><span class="box"></span>No</span></span></div>
  </div>

  <div class="field" style="left:285px;top:495px;width:235px;font-size:9px">Other :<span class="line"></span></div>
  <div class="rule" style="left:316px;top:524px;width:204px"></div>
  <div class="rule" style="left:316px;top:543px;width:204px"></div>
  <div class="field" style="left:285px;top:602px;width:235px;font-size:9px">Signature :<span class="line"></span></div>
  <div class="field" style="left:285px;top:628px;width:235px;font-size:9px">Date :<span class="line"></span></div>

  <div class="brand abs" style="left:28px;top:692px">harbour dental</div>
  <p class="thanks">Thank you for the time to complete your medical history form.<br>Oral health is linked overall health and this comprehensive questionnaire will help us to provide you with optimal ans safe care.</p>

  <div class="footer">
    <svg class="band" width="549" height="15" viewBox="0 0 549 15"><rect width="549" height="15" fill="var(--band-light)"/><polygon points="172,0 549,0 549,15 165,15" fill="var(--band-dark)"/></svg>
    <div class="phone"><svg class="icon" width="10" height="10" viewBox="0 0 10 10"><circle cx="5" cy="5" r="4.4" fill="none" stroke="#1d1d1d"/><path d="M3.3 2.6c.3-.3.6-.2.8.1l.4.7c.1.3 0 .5-.2.6l-.3.2c.2.6.7 1.1 1.2 1.3l.2-.3c.2-.2.4-.3.6-.2l.7.4c.3.2.3.5.1.8-.4.5-1 .6-1.6.3C4 6.1 3.4 5.4 3 4.6c-.3-.7-.2-1.4.3-2z" fill="#1d1d1d"/></svg><span>(02) 4000 1234</span></div>
    <div class="addr"><svg class="icon" width="7" height="10" viewBox="0 0 7 10"><path d="M3.5 0A3.3 3.3 0 0 0 .2 3.3C.2 5.8 3.5 10 3.5 10s3.3-4.2 3.3-6.7A3.3 3.3 0 0 0 3.5 0zm0 4.6a1.3 1.3 0 1 1 0-2.6 1.3 1.3 0 0 1 0 2.6z" fill="#fff"/></svg><span>Harbour Dental, Suite 4/88 Ocean View Rd, Bayside NSW. 2000</span></div>
  </div>
</section>

</body>
</html>
```